Business Card Design for company

We want new business cards. We'd like something different-- yet still highly professional. Our tagline is Providing leadership, delivering success. Stock photos are ok, as long as they are relevant and look upscale.

Target Market(s)

Architecture/Business Management Consulting/Engineering Consulting

Contact Information for Business Card

dark gray background with pops of blue might be good, but you tell me. You're the designers. Rounded corners might be nice, but again, you tell me.

Font styles to use
Serif
Sans Serif

Colors
3276b5
5c5c5c
9d9d9d
fbfbfb

Requirements
Nice to have
• Something different, but still very professional.

```html
<!DOCTYPE html>
<html lang="en">
<head>
<meta charset="utf-8">
<title>Norvale Advisory — Business Card</title>
<link href="https://fonts.googleapis.com/css2?family=Oswald:wght@600&family=Work+Sans:wght@400;500;600&display=swap" rel="stylesheet">
<style>
  :root {
    --blue: #3276b5;
    --blue-deep: #215a91;
    --ink: #5c5c5c;
    --mute: #9d9d9d;
    --paper: #fbfbfb;
    --slate: #3b404b;
    --slate-dark: #30343d;
    --stage: #e6e7ea;
  }
  * { box-sizing: border-box; margin: 0; padding: 0; }
  html, body { width: 1200px; height: 900px; overflow: hidden; }
  body {
    background: var(--stage);
    font-family: "Work Sans", sans-serif;
    display: flex;
    flex-direction: column;
    align-items: center;
    justify-content: center;
    gap: 60px;
  }
  .card {
    width: 600px;
    height: 343px;
    border-radius: 6px;
    position: relative;
    box-shadow: 0 10px 30px rgba(0,0,0,.18);
    overflow: hidden;
  }

  /* Front */
  .card-front { background: linear-gradient(135deg, #ffffff 0%, var(--paper) 60%, #eeeff1 100%); }
  .identity {
    position: absolute;
    left: 70px;
    top: 96px;
    text-align: right;
  }
  .person-name {
    font-family: "Oswald", sans-serif;
    font-weight: 600;
    font-size: 34px;
    letter-spacing: .5px;
    color: var(--blue-deep);
    text-transform: uppercase;
    line-height: 1.1;
  }
  .person-role {
    font-size: 14px;
    color: var(--ink);
    margin-top: 2px;
  }
  .divider {
    position: absolute;
    left: 326px;
    top: 112px;
    width: 2px;
    height: 66px;
    background: var(--blue);
  }
  .contact-list {
    position: absolute;
    left: 344px;
    top: 116px;
    list-style: none;
    font-size: 15px;
    color: var(--ink);
  }
  .contact-list li {
    display: flex;
    align-items: center;
    gap: 8px;
    height: 21px;
  }
  .contact-list svg { width: 11px; height: 11px; flex: none; }
  .web-name { color: var(--blue-deep); font-weight: 500; }
  .address {
    position: absolute;
    left: 70px;
    bottom: 52px;
    font-size: 14px;
    color: var(--ink);
    letter-spacing: .3px;
  }

  /* Back */
  .card-back { background: linear-gradient(160deg, var(--slate) 0%, var(--slate-dark) 100%); }
  .brand {
    position: absolute;
    left: 0; right: 0;
    top: 118px;
    display: flex;
    justify-content: center;
    align-items: center;
    gap: 14px;
  }
  .brand-square { width: 22px; height: 22px; background: var(--blue); }
  .brand-name {
    font-weight: 600;
    font-size: 34px;
    letter-spacing: 4px;
    color: #c9cbcf;
    text-transform: uppercase;
  }
  .web-row {
    position: absolute;
    left: 0; right: 0;
    top: 210px;
    display: flex;
    justify-content: center;
    align-items: center;
    gap: 16px;
    font-size: 14px;
    color: #c9cbcf;
    letter-spacing: .5px;
  }
  .web-row .rule { width: 110px; height: 1px; background: var(--mute); }
</style>
</head>
<body>
  <section class="card card-front" aria-label="Card front">
    <div class="identity">
      <h1 class="person-name">Daniel Reeve</h1>
      <p class="person-role">Director</p>
    </div>
    <span class="divider"></span>
    <ul class="contact-list">
      <li>
        <svg viewBox="0 0 12 12" aria-hidden="true"><path d="M2.5 1 L4.5 1 L5.2 3.6 L4 4.6 C4.7 6 6 7.3 7.4 8 L8.4 6.8 L11 7.5 L11 9.5 C11 10.3 10.3 11 9.5 11 C5 11 1 7 1 2.5 C1 1.7 1.7 1 2.5 1 Z" fill="#3276b5"/></svg>
        (514) 555-0142
      </li>
      <li>
        <svg viewBox="0 0 12 12" aria-hidden="true"><rect x="1" y="2.5" width="10" height="7" fill="none" stroke="#3276b5" stroke-width="1.3"/><path d="M1 3 L6 6.6 L11 3" fill="none" stroke="#3276b5" stroke-width="1.3"/></svg>
        info@norvaleadvisory.com
      </li>
      <li>
        <svg viewBox="0 0 12 12" aria-hidden="true"><circle cx="6" cy="6" r="5" fill="none" stroke="#3276b5" stroke-width="1.2"/><ellipse cx="6" cy="6" rx="2.2" ry="5" fill="none" stroke="#3276b5" stroke-width="1"/><path d="M1 6 H11" stroke="#3276b5" stroke-width="1"/></svg>
        <span>www.<span class="web-name">norvaleadvisory</span>.com</span>
      </li>
    </ul>
    <p class="address">48 Calder Lane, Westbrook, NZ, 8042</p>
  </section>

  <section class="card card-back" aria-label="Card back">
    <div class="brand">
      <span class="brand-square"></span>
      <span class="brand-name">Norvale Advisory</span>
    </div>
    <div class="web-row">
      <span class="rule"></span>
      <span>www.norvaleadvisory.com</span>
      <span class="rule"></span>
    </div>
  </section>
</body>
</html>
```